Home Page Design (+50 More Pages To Winning Designer!)

We have a 50+ page website, but we're starting with the home page. The winning designer will get all 50+ pages to design as a 2nd project, so make sure you do your best!

Velorane is in the private jet industry and needs a re-designed website.

We have created the structure for the website and content inside of Frandle.io (THESE ARE ONLY ROUGH A.I. GENERATED WIREFRAMES AND DO NOT NEED TO BE FOLLOWED EXACTLY) - https://www.frandle.io/app/project/K482915_qWmRtZaLs-KDnHoUvvy82QJ5cfhaR61trkwqlDV3Hm

Take the content from the 'Home Page' under the 'Wireframe' tab on the Frandle.io link above, but feel free to re-design the page in a better way as these are only A.I. generated wireframes.

We want a DARK theme.... High quality, luxurious feel, greyscale colors. Attached is a brand guideline (BUT THIS IS NOT A 100% BRAND GUIDELINE, YOU CAN CHANGE COLORS AND FONTS AND MAKE CHANGES IF YOU HAVE BETTER IDEAS) and attached is our logo. We are also attaching some examples of other apps and websites to give you a guideline of what we're looking for for this design project.

The final design MUST communicate luxury using high-quality imagery of large cabin luxurious private jets.
Updates

ENTRIES THAT DO NOT FOLLOW THE PROJECT BRIEF WILL BE AUTOMATICALLY DISCARDED. FOLLOW THE INSTRUCTIONS!

Industry/Entity Type

Travel

Number of Pages Required

1 page

Font styles to use
Sans Serif

Colors

Designer to choose colors to be used in the design.

Requirements
Must have
• Follow wireframe and use content in wireframe (see Frandle.io link)

```html
<!DOCTYPE html>
<html lang="en">
<head>
<meta charset="utf-8">
<title>Velorane — Luxury Private Jet Travel</title>
<link href="https://fonts.googleapis.com/css2?family=Manrope:wght@300;400;500;600&display=swap" rel="stylesheet">
<style>
:root{
  --ink:#0f0f10;
  --dark:#1c1c1d;
  --dark-2:#262627;
  --grey:#575758;
  --grey-2:#6a6a6b;
  --mid:#8a8a8b;
  --light:#f4f4f4;
  --white:#ffffff;
  --line:rgba(255,255,255,.45);
  --muted:rgba(255,255,255,.6);
  --gold:#e3b53a;
}
*{box-sizing:border-box;margin:0;padding:0}
html,body{width:1200px;height:5051px;overflow:hidden}
body{font-family:"Manrope",sans-serif;color:var(--white);background:var(--ink);position:relative}
section,header,footer{position:relative;width:1200px;overflow:hidden}
.abs{position:absolute}
.h1{font-weight:300;font-size:40px;line-height:1.15;letter-spacing:-.3px}
.h2{font-weight:300;font-size:31px;line-height:1.32}
.eyebrow{font-size:9px;letter-spacing:1.6px;font-weight:500;display:flex;align-items:center;gap:8px}
.eyebrow::after{content:"";width:46px;height:1px;background:currentColor;opacity:.7}
.body{font-size:10.5px;line-height:1.55;color:var(--muted)}
.btn{display:inline-flex;align-items:center;justify-content:center;height:30px;padding:0 22px;font-size:9.5px;letter-spacing:1.2px;font-weight:600;border:1px solid var(--line);color:var(--white);text-transform:uppercase;margin-right:12px;min-width:118px}
.btn.solid{background:var(--white);color:var(--ink);border-color:var(--white)}
.btn.dark{background:var(--ink);color:var(--white);border-color:var(--ink)}
.btn.outline-dark{color:var(--ink);border-color:#9a9a9a}
.photo{position:absolute}
.nav{position:absolute;top:0;left:0;width:1200px;height:62px;display:flex;align-items:center;padding:0 112px;z-index:2}
.brand{font-size:27px;font-weight:300;letter-spacing:-.5px;display:flex;align-items:center;gap:8px}
.brand i{display:inline-block;width:14px;height:14px;border-radius:50%;background:var(--white)}
.menu{display:flex;gap:26px;margin-left:52px;font-size:10.5px;font-weight:500;white-space:nowrap}
.menu span::after{content:" ⌄";font-size:9px}
.inquire{margin-left:auto;border:1px solid var(--white);height:30px;width:114px;display:flex;align-items:center;justify-content:center;font-size:9.5px;letter-spacing:1px;font-weight:600;gap:6px}
.search{height:149px;background:var(--white);color:var(--ink)}
.field{position:absolute;top:80px;height:30px;border:1px solid #cfcfcf;font-size:9.5px;color:#9a9a9a;display:flex;align-items:center;justify-content:space-between;padding:0 10px}
.radio{display:inline-flex;align-items:center;gap:5px;font-size:9.5px;margin-left:14px}
.radio b{width:9px;height:9px;border-radius:50%;border:1px solid #888;display:inline-block}
.radio b.on{background:var(--ink);border-color:var(--ink)}
.checks{display:flex;gap:18px;font-size:10.5px}
.checks span{display:flex;align-items:center;gap:6px}
.checks span::before{content:"";width:10px;height:10px;border-radius:50%;background:var(--white)}
.feat{position:absolute;top:77px;width:270px}
.feat .ico{width:58px;height:58px;border-radius:50%;border:1px solid var(--line);display:flex;align-items:center;justify-content:center}
.feat h3{font-size:14px;font-weight:500;margin:22px 0 10px}
.card{position:absolute;top:202px;height:165px;width:316px;border:1px solid var(--line);padding:34px 28px}
.card h3{font-size:14px;font-weight:500;margin:20px 0 8px}
.q{position:absolute;left:112px;width:498px;height:40px;border:1px solid var(--line);display:flex;align-items:center;justify-content:space-between;padding:0 24px;font-size:12px;font-weight:500}
.logo-box{position:absolute;top:106px;width:144px;height:66px;border:1px solid #d4d4d4;display:flex;align-items:center;justify-content:center;gap:8px;font-size:17px;font-weight:600;color:var(--ink)}
.logo-box i{width:14px;height:14px;background:var(--ink);display:inline-block}
.foot h4{font-size:13px;font-weight:500;margin-bottom:14px}
.foot p{font-size:9.5px;color:var(--muted);line-height:1.95}
</style>
</head>
<body>

<header style="height:563px;background:linear-gradient(90deg,#0d0d0d 0%,#151515 50%,#1d1c1a 100%)">
  <div class="photo" role="img" aria-label="Private jet parked on the tarmac at sunset" style="left:640px;top:0;width:560px;height:563px;background:radial-gradient(ellipse at 60% 60%,rgba(120,100,72,.55) 0%,rgba(50,46,40,.4) 40%,rgba(13,13,13,0) 75%)"></div>
  <nav class="nav">
    <div class="brand">Velorane <i></i></div>
    <div class="menu"><span>Aircraft</span><span>Programs</span><span>Why Velorane</span><span>Lifestyle</span><span>Sustainability</span><span>Resources</span><span>Competitors</span></div>
    <div class="inquire">INQUIRE <svg width="10" height="10" viewBox="0 0 10 10"><path d="M1 5 9 1 6 9 5 6Z" fill="#fff"/></svg></div>
  </nav>
  <div class="abs" style="left:112px;top:188px;width:470px">
    <h1 class="h1">Experience the Ultimate<br>in Luxury Jet Travel</h1>
    <p class="body" style="color:#fff;margin-top:16px;font-size:10px;width:420px">Velorane offers fractional jet ownership, jet card programs, private jet lease programs, all access programs, helicopter access programs, and by the seat charter flights. Discover the perfect flight program for your needs.</p>
    <div style="margin-top:24px"><span class="btn solid">Explore</span><span class="btn">Learn More</span></div>
  </div>
</header>

<section class="search">
  <div class="abs" style="left:112px;top:40px;display:flex;align-items:center"><span style="font-size:17px;font-weight:400">Search Your Flight</span><span class="radio" style="margin-left:20px"><b class="on"></b>Round Trip</span><span class="radio"><b></b>One Way</span></div>
  <div class="field" style="left:112px;width:163px">Departure Airport <span>✈</span></div>
  <div class="field" style="left:292px;width:161px">Arrival Airport <span>✈</span></div>
  <div class="field" style="left:465px;width:163px">Departure Date <span>▦</span></div>
  <div class="field" style="left:641px;width:163px">Return Date <span>▦</span></div>
  <div class="field" style="left:818px;width:88px">Pax <span>⌄</span></div>
  <div class="field" style="left:920px;width:129px;background:var(--ink);border-color:var(--ink);color:#fff;justify-content:center;font-size:10px;letter-spacing:1.2px;font-weight:600">SEARCH</div>
</section>

<section style="height:537px;background:radial-gradient(ellipse at 70% 40%,#6a6a6a,#4b4b4b 70%)">
  <div class="photo" role="img" aria-label="Businessman in a suit standing in front of a private jet" style="left:112px;top:63px;width:298px;height:337px;background:linear-gradient(160deg,#cfd3d8,#8b8f95 55%,#3a3a3c)"></div>
  <div class="photo" role="img" aria-label="Private jet viewed head-on in black and white" style="left:286px;top:245px;width:241px;height:226px;border:1px solid #ddd;background:linear-gradient(180deg,#9d9d9d,#e2e2e2 60%,#6e6e6e)"></div>
  <div class="abs" style="left:588px;top:128px;width:470px">
    <div class="eyebrow">DISCOVER</div>
    <h2 class="h2" style="margin-top:14px">Experience the Luxury of<br>Fractional Jet Ownership</h2>
    <p class="body" style="color:#fff;margin-top:10px;font-size:10px;width:430px">With Velorane's fractional jet ownership program, you can enjoy the benefits of private jet travel without the hassle and expense of owning a whole aircraft. Our program offers flexibility, convenience, and access to a fleet of luxurious jets, allowing you to travel in style and comfort.</p>
    <div class="checks" style="margin-top:16px"><span>Flexible Ownership Options</span><span>Convenient Booking Process</span><span>Luxurious Fleet of Jets</span></div>
    <div style="margin-top:26px"><span class="btn solid">Learn More</span><span class="btn">Sign Up</span></div>
  </div>
</section>

<section style="height:228px;background:var(--ink)">
  <div class="feat" style="left:112px"><div class="ico"><svg width="26" height="26" viewBox="0 0 26 26" fill="none" stroke="#fff" stroke-width="1.3"><path d="M3 15 22 8l-4 6-9 3Z"/><path d="M5 20h16"/></svg></div><h3>Flexible Ownership Options Available</h3><p class="body">Choose from a variety of ownership programs and enjoy the freedom to fly on your own terms.</p></div>
  <div class="feat" style="left:469px"><div class="ico"><svg width="26" height="26" viewBox="0 0 26 26" fill="none" stroke="#fff" stroke-width="1.3"><circle cx="11" cy="8" r="4"/><path d="M3 21c0-5 4-7 8-7"/><rect x="14" y="15" width="9" height="7" rx="1"/></svg></div><h3>Convenient Jet Card Programs</h3><p class="body">Access a fleet of private jets with our exclusive jet card programs, offering flexibility and conve</p></div>
  <div class="feat" style="left:826px"><div class="ico"><svg width="26" height="26" viewBox="0 0 26 26" fill="none" stroke="#fff" stroke-width="1.3"><path d="M4 18 18 4l4 4L8 22Z"/><path d="M10 12l4 4"/></svg></div><h3>Flexible Lease Programs</h3><p class="body">Experience the luxury of private jet travel without the commitment with our flexible lease programs.</p></div>
</section>

<section style="height:543px;background:linear-gradient(90deg,#555556,#6c6c6d)">
  <div class="photo" role="img" aria-label="Private jet flying above the clouds" style="left:833px;top:0;width:367px;height:543px;background:linear-gradient(180deg,#f2f3f5,#c9ccd0 50%,#eef0f2)"></div>
  <div class="photo" role="img" aria-label="Private jet in flight crossing into the clouds" style="left:455px;top:130px;width:500px;height:320px;background:radial-gradient(ellipse at 55% 55%,rgba(210,214,220,.55),rgba(255,255,255,0) 65%)"></div>
  <div class="abs" style="left:112px;top:75px;width:480px">
    <div class="eyebrow">EXPERIENCE</div>
    <h2 class="h2" style="margin-top:14px">Unparalleled Luxury and<br>Convenience for Private Aviation</h2>
    <p class="body" style="color:#fff;margin-top:14px;font-size:10px;width:450px">Discover the ultimate in luxury and convenience with Velorane. Our exclusive private aviation solutions provide you with unparalleled access to the world of private jets, ensuring a seamless and extraordinary travel experience.</p>
    <div style="display:flex;gap:52px;margin-top:22px">
      <div style="width:200px"><div class="checks"><span>Convenience</span></div><p class="body" style="color:#fff;font-size:10px;margin:8px 0 0 18px">Enjoy hassle-free travel with our flexible scheduling and personalized services.</p></div>
      <div style="width:170px"><div class="checks"><span>Luxury</span></div><p class="body" style="color:#fff;font-size:10px;margin:8px 0 0 18px">Indulge in the lavish amenities and exquisite interiors of our private jets.</p></div>
    </div>
    <div style="margin-top:24px"><span class="btn solid">Learn More</span><span class="btn">Sign Up</span></div>
  </div>
</section>

<section style="height:429px;background:var(--dark-2)">
  <div class="abs" style="left:112px;top:60px"><div class="eyebrow">LUXURY</div><h2 class="h2" style="margin-top:14px">Experience the Ultimate<br>in Private Jet Travel</h2></div>
  <div class="abs" style="left:588px;top:60px;width:470px"><p class="body" style="font-size:10px">Velorane offers a wide range of exclusive services to meet your private jet travel needs. From fractional jet ownership to on-demand charter flights, we provide the highest level of luxury and convenience.</p><div style="margin-top:16px"><span class="btn solid">Learn More</span><span class="btn">Sign Up</span></div></div>
  <div class="card" style="left:112px"><svg width="26" height="28" viewBox="0 0 26 28" fill="none" stroke="#fff" stroke-width="1.3"><circle cx="13" cy="10" r="7"/><path d="M9 16l-2 10 6-3 6 3-2-10"/></svg><h3>On-Demand Charter</h3><p class="body">Fly anywhere, anytime with our on-demand charter service.</p></div>
  <div class="card" style="left:441px"><svg width="28" height="28" viewBox="0 0 28 28" fill="none" stroke="#fff" stroke-width="1.3"><circle cx="14" cy="14" r="11"/><ellipse cx="14" cy="14" rx="5" ry="11"/><path d="M3 14h22M5 8h18M5 20h18"/></svg><h3>Global Medical Response &amp; Recovery</h3><p class="body">We provide specialized medical transportation services worldwide.</p></div>
  <div class="card" style="left:771px"><svg width="28" height="28" viewBox="0 0 28 28" fill="none" stroke="#fff" stroke-width="1.3"><circle cx="18" cy="9" r="5"/><path d="M14 13 4 23l2 2 3-3 2 2 2-2-2-2 4-4"/></svg><h3>Fractional Jet Ownership</h3><p class="body">Enjoy the benefits of owning a private jet without the hassles.</p></div>
</section>

<section style="height:247px;background:linear-gradient(180deg,#ffffff 40%,#e4e6e9);color:var(--ink);text-align:center">
  <div class="photo" role="img" aria-label="Soft clouds along the lower edge" style="left:0;top:140px;width:1200px;height:107px;background:linear-gradient(180deg,rgba(255,255,255,0),#cfd3d8)"></div>
  <h2 class="h2" style="position:relative;padding-top:62px">Experience luxury travel like never before</h2>
  <p style="position:relative;font-size:10px;margin-top:4px">Contact us today to book your exclusive jet experience</p>
  <div style="position:relative;margin-top:22px"><span class="btn dark">Learn More</span><span class="btn outline-dark" style="margin-right:0">Sign Up</span></div>
</section>

<section style="height:477px;background:linear-gradient(180deg,#fafafa,#e9eaec);color:var(--ink)">
  <p class="abs" style="left:112px;top:98px;width:500px;font-size:29px;font-weight:300;line-height:1.45">“Velorane's services have exceeded my expectations. The convenience and luxury of flying with them is unmatched.”</p>
  <div class="abs" style="left:112px;top:275px;color:var(--gold);font-size:17px;letter-spacing:8px">★★★★★</div>
  <div class="abs" style="left:112px;top:318px"><div style="font-size:17px">Marcus Hale</div><div style="font-size:8.5px;color:#555;margin-top:4px">CEO, Norvane Corp</div></div>
  <div class="abs" style="left:208px;top:318px;width:1px;height:40px;background:#bbb"></div>
  <div class="abs" style="left:230px;top:329px;font-size:14px;font-weight:600;display:flex;gap:6px;align-items:center"><i style="width:12px;height:12px;background:var(--ink);display:inline-block"></i>Quellix</div>
  <div class="photo" role="img" aria-label="Businessman in sunglasses stepping away from a private jet engine" style="left:673px;top:61px;width:415px;height:330px;background:linear-gradient(120deg,#2a2b2d,#6b6d70 45%,#a7a9ac)"></div>
  <div class="abs" style="left:749px;top:359px;width:129px;height:55px;background:var(--ink);display:flex;align-items:center;justify-content:space-around;color:#fff;font-size:20px"><span>⟵</span><span>⟶</span></div>
</section>

<section style="height:235px;background:var(--white);color:var(--ink)">
  <p class="abs" style="left:0;width:1200px;top:56px;text-align:center;font-size:19px;font-weight:300">Trusted by top-tier companies around the globe</p>
  <div class="abs" style="left:100px;top:128px;font-size:16px">‹</div>
  <div class="abs" style="left:1090px;top:128px;font-size:16px">›</div>
  <div class="logo-box" style="left:122px"><i></i>Quellix</div>
  <div class="logo-box" style="left:283px"><i></i>Frandle</div>
  <div class="logo-box" style="left:446px"><i></i>Quellix</div>
  <div class="logo-box" style="left:609px"><i></i>Frandle</div>
  <div class="logo-box" style="left:771px"><i></i>Quellix</div>
  <div class="logo-box" style="left:934px"><i></i>Frandle</div>
</section>

<section style="height:435px;background:var(--grey)">
  <div class="photo" role="img" aria-label="Private jet flying over a coastline and sea" style="left:0;top:0;width:367px;height:435px;background:linear-gradient(160deg,#c7ccd1,#7e8b93 55%,#3e4a50)"></div>
  <div class="abs" style="left:588px;top:142px">
    <h2 class="h2">Subscribe to Our Newsletter</h2>
    <p style="font-size:9.5px;margin-top:4px">Stay updated with exclusive offers and industry news</p>
    <div style="display:flex;margin-top:26px"><div style="width:287px;height:31px;border:1px solid var(--line);font-size:9.5px;color:var(--muted);display:flex;align-items:center;padding-left:12px">Your email address</div><div style="width:119px;height:31px;background:#fff;color:var(--ink);font-size:9.5px;font-weight:600;letter-spacing:1px;display:flex;align-items:center;justify-content:center">JOIN NOW</div></div>
    <p style="font-size:9.5px;margin-top:14px">By joining, you agree to our <u>Terms and Conditions</u></p>
  </div>
  <div class="abs" style="left:586px;top:355px;font-size:92px;font-weight:300;color:rgba(255,255,255,.08);letter-spacing:-2px;line-height:1">Velorane</div>
</section>

<section style="height:667px;background:var(--dark-2)">
  <h2 class="abs h2" style="left:112px;top:66px">Frequently Asked Questions</h2>
  <p class="abs body" style="left:112px;top:116px;font-size:9.5px">Find answers to common questions about Velorane's services and programs.</p>
  <div class="q" style="top:153px">What is Velorane?<span>+</span></div>
  <div class="abs" style="left:112px;top:207px;width:498px;height:107px;background:#fff;color:var(--ink);padding:16px 24px"><div style="font-size:12px;font-weight:500">How it works?</div><p style="font-size:9.5px;line-height:1.55;margin-top:6px;color:#333">Velorane works by allowing customers to purchase fractional ownership of a private jet, join jet card programs for a set number of flight hours, lease a private jet for a specific period, or access our all access and helicopter programs. We also offer charter flights where customers can book individual seats on flights.</p></div>
  <div class="q" style="top:330px">Why choose Velorane?<span>+</span></div>
  <div class="q" style="top:383px">How to book?<span>+</span></div>
  <div class="q" style="top:436px">What are the benefits?<span>+</span></div>
  <div class="abs" style="left:112px;top:502px"><div style="font-size:13px">Still have questions?</div><p class="body" style="font-size:9.5px;margin-top:2px">Contact us for more information.</p><div style="margin-top:20px"><span class="btn solid">Learn More</span><span class="btn">Sign Up</span></div></div>
  <div class="photo" role="img" aria-label="Woman on the phone seated in a private jet cabin" style="left:680px;top:63px;width:404px;height:530px;border:2px solid #ddd;background:linear-gradient(150deg,#e9dfd1,#b79f83 50%,#5d4a3a)"></div>
</section>

<section style="height:259px;background:linear-gradient(180deg,#3a3836,#1c1b1a);text-align:center">
  <div class="photo" role="img" aria-label="Private jet cabin interior in low light" style="left:0;top:0;width:1200px;height:259px;background:radial-gradient(ellipse at 50% 20%,rgba(150,130,105,.35),rgba(0,0,0,0) 60%)"></div>
  <h2 class="h2" style="position:relative;padding-top:56px">Experience luxury travel like never before</h2>
  <p style="position:relative;font-size:9.5px;width:760px;margin:6px auto 0;line-height:1.55">Discover the ultimate in private jet travel with Velorane. Whether you're looking for fractional jet ownership, jet card programs, private jet lease programs, all access programs, helicopter access programs, or by the seat charter flights, we have the perfect solution for your travel needs.</p>
  <div style="position:relative;margin-top:22px"><span class="btn solid">Book</span><span class="btn" style="margin-right:0">Contact</span></div>
</section>

<footer style="height:282px;background:var(--ink)">
  <div class="abs brand" style="left:112px;top:52px">Velorane <i></i></div>
  <div class="abs" style="left:112px;top:106px;font-size:13px">Follow Us:</div>
  <div class="abs" style="left:112px;top:130px;display:flex;gap:8px"><i style="width:20px;height:20px;border:1px solid #fff;border-radius:50%"></i><i style="width:20px;height:20px;border:1px solid #fff;border-radius:50%"></i><i style="width:20px;height:20px;border:1px solid #fff;border-radius:50%"></i><i style="width:20px;height:20px;border:1px solid #fff;border-radius:50%"></i><i style="width:20px;height:20px;border:1px solid #fff;border-radius:50%"></i></div>
  <div class="abs foot" style="left:345px;top:58px"><h4>About Us</h4><p>Charter<br>Fleet<br>Destinations<br>Pricing<br>Contact</p></div>
  <div class="abs foot" style="left:482px;top:58px"><h4>Services</h4><p>Private Jets<br>Helicopters<br>Jet Cards<br>Membership<br>FAQ</p></div>
  <div class="abs foot" style="left:633px;top:58px"><h4>Terms</h4><p>Terms<br>Privacy<br>Careers<br>Press<br>Blog<br>Support</p></div>
  <div class="abs foot" style="left:771px;top:58px;width:317px"><h4>Subscribe to Our Newsletter</h4><p style="line-height:1.4">Join our mailing list for the latest updates.</p>
    <div style="display:flex;margin-top:12px"><div style="width:210px;height:31px;border:1px solid var(--line);font-size:9.5px;color:var(--muted);display:flex;align-items:center;padding-left:12px">Enter Your Email</div><div style="width:99px;height:31px;margin-left:8px;background:#fff;color:var(--ink);font-size:9.5px;font-weight:600;letter-spacing:1px;display:flex;align-items:center;justify-content:center">SUBSCRIBE</div></div>
    <p style="line-height:1.5;margin-top:10px">By subscribing, you agree to our Privacy Policy and consent to receive updates.</p></div>
  <div class="abs" style="left:112px;top:210px;width:976px;height:1px;background:rgba(255,255,255,.3)"></div>
  <p class="abs" style="left:0;width:1200px;top:236px;text-align:center;font-size:9px;color:var(--muted)">© 2024 Velorane. All rights reserved. &nbsp; | &nbsp; Privacy Policy &nbsp; | &nbsp; Terms of Service &nbsp; | &nbsp; Cookie Settings</p>
</footer>

</body>
</html>
```